Book cover - Lanterns Along the Winding Quay

Book cover for Ebook (Quillet) and wrap around print cover (Bindwell) (back, front, and spine)

The book title (may slightly change by end of brief):
(MAIN TITLE) 'Lanterns Along the Winding Quay'
(SUB HEADING) 'A Practical Seasonal Garden Companion for Planting Bulbs, Pruning Hedges and Growing Fresh Herbs'
by Dr Owen Pratchard

I would like a bold, stand out cover. Contemporary. I would like to avoid stereotypical images of people looking anxious or worried. I would like the design to be more uplifting and hopeful, rather than focusing on the negative aspect of anxiety, but avoiding cliched photos of people raising their hands in the air, smiling and jumping etc. The cover should appeal to both men and women.

Trim size of book cover (for BindWell) is 5.25" x 8" back and front with a spine size of 0.477 inches
Updates

Reason: I have decided to extend the deadline by 1 more day, not because I am unhappy with the quality of the designs, but because a few designers have contacted me to explain they have had technical difficulties when submitting their files. Thanks everyone for the hard work and great designs.

Target Market(s)

Males and females (16+) who struggle with social anxiety and shyness

Industry/Entity Type

Social

Font styles to use
Serif

Requirements
Must have
• Bold cover that is modern and contemporary. For example, I like these covers:
• http://lnkvo.test/7kTq3Wm
• http://lnkvo.test/9gHw5Ze
• http://lnkvo.test/4nVy8Kb
• http://lnkvo.test/6jFu2Xo
• http://lnkvo.test/3mEs9Lt
• http://lnkvo.test/8hGz4Nd
• http://lnkvo.test/5bJk7Pv
Nice to have
• Open to abstract designs.
Should not have
• No stereotypical pictures of people who look anxious or worried. Avoid cliched photos of people raising their hands in the air, smiling and jumping etc.

```html
<!DOCTYPE html>
<html lang="en">
<head>
<meta charset="utf-8">
<title>Lanterns Along the Winding Quay – Cover</title>
<link rel="stylesheet" href="https://fonts.googleapis.com/css2?family=Kalam:wght@700&family=Arimo:wght@700&display=swap">
<style>
  :root {
    --page-bg: #ffffff;
    --cover-blue: #1414f0;
    --cover-blue-light: #2a2cff;
    --band-cyan: #16c4dd;
    --band-cyan-light: #3cd8ec;
    --ice-white: #f4f8fa;
    --ice-pale: #d6e8f0;
    --ice-blue: #8cc6dc;
    --ice-deep: #5aa6c6;
    --text-light: #ffffff;
    --text-navy: #0a1446;
  }
  * { margin: 0; padding: 0; box-sizing: border-box; }
  html, body {
    width: 1200px;
    height: 1200px;
    overflow: hidden;
    background: var(--page-bg);
  }
  .cover {
    position: absolute;
    left: 242px;
    top: 88px;
    width: 740px;
    height: 1006px;
    background: linear-gradient(180deg, var(--cover-blue-light) 0%, var(--cover-blue) 100%);
    overflow: hidden;
  }
  .band {
    position: absolute;
    left: 0;
    width: 100%;
    background: linear-gradient(180deg, var(--band-cyan-light), var(--band-cyan));
  }
  .band--top { top: 0; height: 56px; }
  .band--bottom {
    bottom: 0;
    height: 85px;
    display: flex;
    align-items: center;
    justify-content: center;
  }
  .cover-photo {
    position: absolute;
    left: 50px;
    top: 114px;
    width: 642px;
    height: 404px;
    background:
      linear-gradient(152deg, rgba(244,248,250,0) 55%, var(--ice-white) 56%, var(--ice-pale) 100%),
      radial-gradient(ellipse at 72% 38%, var(--ice-white) 0%, rgba(244,248,250,0) 45%),
      linear-gradient(100deg, var(--ice-deep) 0%, var(--ice-blue) 30%, var(--ice-pale) 70%, var(--ice-white) 100%);
  }
  .title-block {
    position: absolute;
    left: 30px;
    right: 30px;
    top: 562px;
    display: flex;
    flex-direction: column;
    align-items: center;
    text-align: center;
    color: var(--text-light);
  }
  .title {
    font-family: "Kalam", cursive;
    font-weight: 700;
    font-size: 64px;
    line-height: 58px;
    letter-spacing: 2px;
    padding-left: 20px;
  }
  .subtitle {
    margin-top: 14px;
    font-family: "Arimo", sans-serif;
    font-weight: 700;
    font-size: 24px;
    line-height: 32px;
    letter-spacing: 1.8px;
    max-width: 580px;
  }
  .author {
    font-family: "Arimo", sans-serif;
    font-weight: 700;
    font-size: 27px;
    letter-spacing: 2.4px;
    color: var(--text-navy);
  }
</style>
</head>
<body>
  <main class="cover">
    <div class="band band--top"></div>
    <div class="cover-photo" role="img" aria-label="Photograph of two penguins on icy blue snow slopes, one leaping down while the other watches from the ledge"></div>
    <section class="title-block">
      <h1 class="title">Lanterns Along<br>the Winding<br>Quay</h1>
      <p class="subtitle">A Practical Seasonal Garden Companion for Planting Bulbs, Pruning Hedges and Growing Fresh Herbs</p>
    </section>
    <footer class="band band--bottom">
      <p class="author">Dr Owen Pratchard</p>
    </footer>
  </main>
</body>
</html>
```